New Interrior Decoration company needs new website

We need a website for our new company specialising in interior decoration to residential and commercial markets.
We supply and install decorative and printed films for office and home decoration such as feature walls.
We would like to keep the design simple and clean.

Target Market(s)

Architects and interior designaers

Industry/Entity Type

It Company

Number of Pages Required

5+ page

Font styles to use
Sans Serif

Requirements
Must have
• Home page,
• Services/products page (split into commercial and residential)
• Gallery (split into commercial and residential)
• contact form and page
Nice to have
• Very clean and minimalistic design.

```html
<!DOCTYPE html>
<html lang="en">
<head>
<meta charset="utf-8">
<title>Northline Interiors</title>
<link href="https://fonts.googleapis.com/css2?family=Raleway:wght@400;500;600;700&family=Open+Sans:wght@400;600;700&display=swap" rel="stylesheet">
<style>
:root{
  --blue:#0062bd;
  --charcoal:#3a3a3a;
  --footer:#3d3d3d;
  --footer-deep:#2e2e2e;
  --ink:#333333;
  --muted:#777777;
  --light:#f3f3f3;
  --white:#ffffff;
  --field:#565656;
}
*{margin:0;padding:0;box-sizing:border-box}
html,body{width:1200px;height:2731px;overflow:hidden}
body{position:relative;background:var(--white);font-family:"Open Sans",sans-serif;color:var(--ink)}
.abs{position:absolute}

/* hero */
.hero{left:0;top:0;width:1200px;height:721px;background:linear-gradient(180deg,#f4f4f4 0%,#e9e9e9 55%,#dadada 100%)}
.nav{left:0;top:22px;width:1200px;height:30px}
.nav a{position:absolute;top:0;font-family:"Raleway",sans-serif;font-size:20px;color:var(--ink);text-decoration:none;letter-spacing:.3px}
.nav a.is-active{color:var(--blue)}
.nav-rule{left:78px;top:73px;width:1046px;height:1px;background:#9a9a9a}
.brand{display:flex;align-items:center;gap:22px;font-family:"Raleway",sans-serif;font-weight:700;color:var(--charcoal)}
.brand-mark{background:var(--blue)}
.hero-brand{left:0;top:300px;width:1200px;justify-content:center}
.hero-brand .brand-mark{width:118px;height:118px}
.hero-brand .brand-name{font-size:60px;line-height:1;letter-spacing:-.5px}

/* services band */
.service{top:721px;width:600px;height:230px;color:var(--white)}
.service--residential{left:0;background:var(--blue)}
.service--commercial{left:600px;background:var(--charcoal)}
.service svg{position:absolute}
.service h2{position:absolute;top:40px;font-family:"Raleway",sans-serif;font-weight:500;font-size:27px}
.service p{position:absolute;top:78px;width:300px;font-size:16px;line-height:25px}
.service .more{position:absolute;top:163px;font-family:"Raleway",sans-serif;font-size:18px;letter-spacing:.3px}

/* welcome */
.welcome{left:0;top:951px;width:1200px;height:324px;text-align:center}
.welcome h1{position:absolute;left:0;top:50px;width:1200px;font-family:"Raleway",sans-serif;font-weight:400;font-size:41px;color:var(--ink)}
.accent{color:var(--blue)}
.welcome p{position:absolute;left:170px;top:114px;width:860px;font-size:15.5px;line-height:25px;color:var(--muted)}
.btn{position:absolute;display:flex;align-items:center;justify-content:center;font-family:"Raleway",sans-serif;font-size:19px;border-radius:3px}
.btn--blue{background:var(--blue);color:var(--white)}
.btn--white{background:var(--white);color:var(--ink);border-radius:0}

/* gallery */
.gallery{left:0;top:1275px;width:1200px;height:661px;background:var(--light)}
.gallery h2{position:absolute;left:0;top:45px;width:1200px;text-align:center;font-family:"Raleway",sans-serif;font-weight:400;font-size:41px;color:var(--ink)}
.tab{position:absolute;top:105px;height:50px;display:flex;align-items:center;justify-content:center;font-family:"Open Sans",sans-serif;font-size:24px;color:var(--white)}
.tab--residential{left:402px;width:188px;background:var(--blue)}
.tab--commercial{left:610px;width:188px;background:var(--charcoal)}
.tile{position:absolute;width:235px;height:155px}

/* contact */
.contact{left:0;top:1936px;width:1200px;height:459px;background:var(--blue)}
.contact h2{position:absolute;left:0;top:50px;width:1200px;text-align:center;font-family:"Raleway",sans-serif;font-weight:400;font-size:41px;color:var(--white)}
.field{position:absolute;background:var(--white);font-size:15px;color:#555;padding:13px 10px}

/* footer */
.footer{left:0;top:2395px;width:1200px;height:284px;background:var(--footer);color:var(--white)}
.footer-brand{left:78px;top:38px;gap:10px;color:var(--white)}
.footer-brand .brand-mark{width:34px;height:34px}
.footer-brand .brand-name{font-size:25px;line-height:1}
.footer-about{left:78px;top:97px;width:240px;font-size:15.5px;line-height:25.5px}
.footer-links{left:348px;top:70px;list-style:none}
.footer-links li{height:36.5px;font-size:18px;display:flex;align-items:center;gap:10px}
.footer-info{left:621px;font-size:15.5px;display:flex;gap:10px;align-items:flex-start;line-height:24px}
.social{position:absolute;top:204px;width:44px;height:44px;border:1.5px solid var(--white);border-radius:3px}
.sub-field{position:absolute;left:889px;width:235px;height:34px;background:var(--field);font-size:15px;padding:7px 9px}
.bottom-bar{left:0;top:2679px;width:1200px;height:52px;background:var(--footer-deep);color:var(--white);font-size:15.5px;display:flex;align-items:center;justify-content:center}
</style>
</head>
<body>

<header class="abs hero" role="img" aria-label="Photo of a bright white living room with sofas, pendant lamps and shelving">
  <nav class="abs nav">
    <a class="is-active" style="left:255px">HOME</a>
    <a style="left:382px">ABOUT</a>
    <a style="left:519px">SERVICES</a>
    <a style="left:685px">GALLERY</a>
    <a style="left:846px">CONTACT</a>
  </nav>
  <div class="abs nav-rule"></div>
  <div class="abs brand hero-brand">
    <span class="brand-mark"></span>
    <span class="brand-name">NORTHLINE<br>INTERIORS</span>
  </div>
</header>

<section class="abs service service--residential">
  <svg style="left:78px;top:49px" width="156" height="126" viewBox="0 0 156 126" aria-hidden="true">
    <path d="M78 4 L4 64 L16 76 L78 26 L140 76 L152 64 L124 41 L124 12 L108 12 L108 28 Z" fill="#fff"/>
    <path d="M28 72 L78 32 L128 72 L128 124 L92 124 L92 88 L64 88 L64 124 L28 124 Z" fill="#fff"/>
  </svg>
  <h2 style="left:255px">Residential Interiors</h2>
  <p style="left:255px">Lorem Ipsum is simply dummy text of the printing and typesetting industry Lorem Ipsum...</p>
  <span class="more" style="left:255px">READ MORE &raquo;</span>
</section>

<section class="abs service service--commercial">
  <svg style="left:52px;top:46px" width="134" height="128" viewBox="0 0 134 128" aria-hidden="true">
    <path d="M38 20 L74 4 L74 124 L38 124 Z" fill="#fff"/>
    <rect x="78" y="40" width="28" height="84" fill="#fff"/>
    <rect x="4" y="64" width="30" height="60" fill="#fff"/>
    <rect x="108" y="88" width="24" height="36" fill="#fff"/>
    <g fill="#3a3a3a">
      <rect x="46" y="30" width="8" height="8"/><rect x="60" y="26" width="8" height="8"/>
      <rect x="46" y="48" width="8" height="8"/><rect x="60" y="48" width="8" height="8"/>
      <rect x="46" y="66" width="8" height="8"/><rect x="60" y="66" width="8" height="8"/>
      <rect x="46" y="84" width="8" height="8"/><rect x="60" y="84" width="8" height="8"/>
      <rect x="10" y="74" width="7" height="7"/><rect x="21" y="74" width="7" height="7"/>
      <rect x="10" y="92" width="7" height="7"/><rect x="21" y="92" width="7" height="7"/>
      <rect x="84" y="52" width="7" height="7"/><rect x="94" y="52" width="7" height="7"/>
      <rect x="84" y="70" width="7" height="7"/><rect x="94" y="70" width="7" height="7"/>
      <rect x="113" y="96" width="6" height="6"/><rect x="122" y="96" width="6" height="6"/>
    </g>
  </svg>
  <h2 style="left:219px">Commercial Interiors</h2>
  <p style="left:219px">Lorem Ipsum is simply dummy text of the printing and typesetting industry Lorem Ipsum...</p>
  <span class="more" style="left:219px">READ MORE &raquo;</span>
</section>

<section class="abs welcome">
  <h1>WELCOME TO <span class="accent">NORTHLINE INTERIORS</span></h1>
  <p>Lorem Ipsum is simply dummy text of the printing and typesetting industry. Lorem Ipsum has been the industry's standard dummy text ever since the 1500s, when an unknown printer took a galley of type and scrambled it to make a type specimen book.</p>
  <span class="btn btn--blue" style="left:519px;top:209px;width:162px;height:53px">READ MORE</span>
</section>

<section class="abs gallery">
  <h2>LATEST <span class="accent">GALLERY</span></h2>
  <span class="tab tab--residential">Residential</span>
  <span class="tab tab--commercial">Commercial</span>

  <div class="tile" style="left:76px;top:180px;background:linear-gradient(135deg,#c9b56a,#8e9a6a 55%,#c4382c)" role="img" aria-label="Living room with a striped feature wall and red chairs"></div>
  <div class="tile" style="left:346px;top:180px;background:linear-gradient(135deg,#5a2a1e,#2a1d1a 60%,#b89aa8)" role="img" aria-label="Dark room with a white lounge chair and floor lamp"></div>
  <div class="tile" style="left:617px;top:180px;background:linear-gradient(135deg,#7b4a3a,#3d5f9a 50%,#e2ddd6)" role="img" aria-label="Office with a colourful printed feature wall"></div>
  <div class="tile" style="left:889px;top:180px;background:linear-gradient(135deg,#d8dcdc,#6e7474 55%,#3b3f3f)" role="img" aria-label="Grey kitchen with pendant lamps"></div>

  <div class="tile" style="left:76px;top:357px;background:linear-gradient(135deg,#4a4440,#9b8e82 55%,#d9d3cb)" role="img" aria-label="Open dining and kitchen area"></div>
  <div class="tile" style="left:346px;top:357px;background:linear-gradient(135deg,#8e9158,#5f6533 60%,#c9c6a8)" role="img" aria-label="Olive green room with a framed print and vases"></div>
  <div class="tile" style="left:617px;top:357px;background:linear-gradient(135deg,#6b3a4a,#4a2635 55%,#e6e2dc)" role="img" aria-label="Lounge with a burgundy wall and white sofa"></div>
  <div class="tile" style="left:889px;top:357px;background:linear-gradient(135deg,#c9b56a,#8e9a6a 55%,#c4382c)" role="img" aria-label="Living room with a striped feature wall and red chairs"></div>

  <span class="btn btn--blue" style="left:524px;top:550px;width:150px;height:51px">VIEW ALL</span>
</section>

<section class="abs contact">
  <h2>GET IN TOUCH WITH US</h2>
  <div class="field" style="left:111px;top:133px;width:311px;height:45px">Enter Name</div>
  <div class="field" style="left:444px;top:133px;width:312px;height:45px">Enter Email</div>
  <div class="field" style="left:778px;top:133px;width:311px;height:45px">Enter Contact No.</div>
  <div class="field" style="left:111px;top:200px;width:978px;height:113px">Enter Message</div>
  <span class="btn btn--white" style="left:528px;top:337px;width:142px;height:51px">SUBMIT</span>
</section>

<footer class="abs footer">
  <div class="abs brand footer-brand">
    <span class="brand-mark"></span>
    <span class="brand-name">NORTHLINE<br>INTERIORS</span>
  </div>
  <p class="abs footer-about">Lorem Ipsum is simply dummy text of the printing and typesetting industry. Lorem Ipsum has been the industry's standard dummy text ever since the 1500.</p>

  <ul class="abs footer-links">
    <li><svg width="18" height="10" viewBox="0 0 18 10" aria-hidden="true"><path d="M0 5H16M12 1L16 5L12 9" stroke="#fff" stroke-width="1.6" fill="none"/></svg>Home</li>
    <li><svg width="18" height="10" viewBox="0 0 18 10" aria-hidden="true"><path d="M0 5H16M12 1L16 5L12 9" stroke="#fff" stroke-width="1.6" fill="none"/></svg>About</li>
    <li><svg width="18" height="10" viewBox="0 0 18 10" aria-hidden="true"><path d="M0 5H16M12 1L16 5L12 9" stroke="#fff" stroke-width="1.6" fill="none"/></svg>Services</li>
    <li><svg width="18" height="10" viewBox="0 0 18 10" aria-hidden="true"><path d="M0 5H16M12 1L16 5L12 9" stroke="#fff" stroke-width="1.6" fill="none"/></svg>Gallery</li>
    <li><svg width="18" height="10" viewBox="0 0 18 10" aria-hidden="true"><path d="M0 5H16M12 1L16 5L12 9" stroke="#fff" stroke-width="1.6" fill="none"/></svg>Contact</li>
  </ul>

  <div class="abs footer-info" style="top:64px;width:240px">
    <svg width="14" height="20" viewBox="0 0 14 20" style="margin-top:3px;flex:none" aria-hidden="true"><path d="M7 0C3 0 0 3 0 7C0 12 7 20 7 20C7 20 14 12 14 7C14 3 11 0 7 0Z" fill="#fff"/><circle cx="7" cy="7" r="2.6" fill="#3d3d3d"/></svg>
    <span>Lorem Ipsum is dummy text of the printing.</span>
  </div>
  <div class="abs footer-info" style="top:121px;font-weight:700">
    <svg width="18" height="18" viewBox="0 0 18 18" style="margin-top:3px" aria-hidden="true"><path d="M4 1L7 5L5 7C6 10 8 12 11 13L13 11L17 14L15 17C8 17 1 10 1 3Z" fill="#fff"/></svg>
    <span>123 456 7890</span>
  </div>
  <div class="abs footer-info" style="top:162px">
    <svg width="18" height="14" viewBox="0 0 18 14" style="margin-top:5px" aria-hidden="true"><rect x="1" y="1" width="16" height="12" rx="1" stroke="#fff" stroke-width="1.6" fill="none"/><path d="M1 2L9 8L17 2" stroke="#fff" stroke-width="1.6" fill="none"/></svg>
    <span>info@northlineinteriors.com</span>
  </div>
  <span class="social" style="left:619px;background:var(--white)"></span>
  <span class="social" style="left:692px"></span>
  <span class="social" style="left:765px"></span>

  <div class="sub-field" style="top:74px">Enter Name</div>
  <div class="sub-field" style="top:125px">Enter Email</div>
  <span class="btn btn--white" style="left:889px;top:178px;width:151px;height:46px;border-radius:3px;font-size:18px">SUBSCRIBE</span>
</footer>

<div class="abs bottom-bar">&copy;&nbsp;<strong>NORTHLINE INTERIORS</strong>&nbsp;- 2016. All Rights Reserved.</div>

</body>
</html>
```